****Business Card Design for Quarrystone Development. Design based around attached logo/company name

I’m looking for business card design for my company Quarrystone Development Group,LLC. Design should be professional, sharp and minimal. Outside of the attached logos, greyscale colors for remainder of cards. My thoughts are two-sided card with attached logo on one side and my info on the other but open to one-sided as well with right design.
Target Market(s)
Real estate professionals including banks, private investors, property owners, developers, commercial tenants like Brewlantern, Grovika or Tanquist’s.
Industry/Entity Type
Commercial real estate development and investments.
Contact Information for Business Card
Name, title, email, phone #’s, web address and physical address
Font styles to use
Other font styles liked:
- Helvetica, Garamond, etc
Colors
Designer to choose only greyscale colors for use in the design.
Requirements
Must have
- Attached logo first or second options.
Nice to have
- Two sided card with logo on one side. Attached Logo/company name can be laid out any way that flows as long as it’s legible.name
Should not have
- No loud colors. ***Please do not include logo, I have removed the company design with a logo image.

```html
<!DOCTYPE html>
<html lang="en">
<head>
<meta charset="utf-8">
<title>Quarrystone Development – Business Card</title>
<link rel="stylesheet" href="https://fonts.googleapis.com/css2?family=Cinzel:wght@400&family=Tinos:wght@400&display=swap">
<style>
  :root {
    --page: #e8e8e8;
    --card-top: #6e7686;
    --card-bottom: #555c6b;
    --ink: #ffffff;
    --rule: rgba(255,255,255,0.55);
  }
  * { margin: 0; padding: 0; box-sizing: border-box; }
  html, body { width: 1200px; height: 1200px; overflow: hidden; background: var(--page); }
  .card {
    position: absolute;
    left: 262px;
    width: 686px;
    height: 392px;
    background: linear-gradient(180deg, var(--card-top), var(--card-bottom));
    color: var(--ink);
  }
  .card--front { top: 165px; }
  .card--back { top: 626px; }

  .contact { position: absolute; left: 48px; top: 72px; font-family: "Tinos", serif; }
  .contact__name { font-size: 21px; letter-spacing: 0.5px; line-height: 1.1; }
  .contact__title { font-size: 16px; line-height: 1.3; }
  .contact__address { margin-top: 22px; font-size: 15.5px; line-height: 20px; }
  .contact__lines { margin-top: 20px; list-style: none; font-size: 15.5px; line-height: 21px; }
  .contact__lines li { display: flex; align-items: center; gap: 10px; }
  .contact__lines svg { width: 13px; height: 13px; fill: var(--ink); flex: none; }

  .front-wordmark {
    position: absolute; left: 46px; top: 315px;
    font-family: "Cinzel", serif; font-size: 40px; line-height: 1;
    letter-spacing: 0.5px;
  }
  .front-accent {
    position: absolute; left: 400px; top: 60px;
    width: 230px; height: 230px; border-radius: 50%;
    border: 2px solid var(--rule);
  }

  .brand {
    position: absolute; inset: 0;
    display: flex; align-items: center; justify-content: center; gap: 22px;
  }
  .brand__dot { width: 58px; height: 58px; border-radius: 50%; background: var(--ink); flex: none; }
  .brand__text { font-family: "Cinzel", serif; color: var(--ink); }
  .brand__name { font-size: 48px; line-height: 1; letter-spacing: 0.5px; }
  .brand__rule { height: 2px; background: var(--rule); margin: 4px 0 5px; }
  .brand__sub { font-size: 21px; line-height: 1; letter-spacing: 1px; }
</style>
</head>
<body>
  <section class="card card--front">
    <div class="contact">
      <p class="contact__name">DANIEL HARROW</p>
      <p class="contact__title">President</p>
      <p class="contact__address">4120 Alder Crest Way<br>Juneau, Alaska 35812</p>
      <ul class="contact__lines">
        <li><svg viewBox="0 0 16 16"><path d="M3.5 1l3 3-1.7 2a9 9 0 0 0 5.2 5.2l2-1.7 3 3-1.8 2.3C7 14.6 1.4 9 .8 3.3z"/></svg>555-214-7730</li>
        <li><svg viewBox="0 0 16 16"><path d="M4 1h8v4H4zM1 6h14v7h-3v2H4v-2H1zm4 4v4h6v-4z"/></svg>555-318-4062</li>
        <li><svg viewBox="0 0 16 16"><path d="M1 3h14v1L8 9 1 4zm0 3l7 5 7-5v7H1z"/></svg>name@quarrystone.com</li>
        <li><svg viewBox="0 0 16 16"><path d="M8 1a7 7 0 1 0 0 14A7 7 0 0 0 8 1zm0 2c.9 1.2 1.4 2.6 1.5 4h-3C6.6 5.6 7.1 4.2 8 3zM4.6 7H3.1A5 5 0 0 1 6 3.3 9 9 0 0 0 4.6 7zm0 2a9 9 0 0 0 1.4 3.7A5 5 0 0 1 3.1 9zm1.9 0h3c-.1 1.4-.6 2.8-1.5 4-.9-1.2-1.4-2.6-1.5-4zm4.9 0h1.5a5 5 0 0 1-2.9 3.7A9 9 0 0 0 11.4 9zm0-2A9 9 0 0 0 10 3.3 5 5 0 0 1 12.9 7z"/></svg>www.quarrystone.com</li>
      </ul>
    </div>
    <div class="front-accent" aria-hidden="true"></div>
    <p class="front-wordmark">QUARRYSTONE</p>
  </section>

  <section class="card card--back">
    <div class="brand">
      <span class="brand__dot" aria-hidden="true"></span>
      <div class="brand__text">
        <p class="brand__name">QUARRYSTONE</p>
        <div class="brand__rule"></div>
        <p class="brand__sub">DEVELOPMENT GROUP, LLC</p>
      </div>
    </div>
  </section>
</body>
</html>
```